Cozy Cradle Loops Needs a Beautiful Website

I need a new website for this new E-commerce. I sell handmade baby crochets, e.g. booties, headbands, hats, etc. I need a feminine and soft design to make the moms-to-be say 'oohh ahh'. I'd like pink, blue and gray. I'd like an inviting homepage, and nice regular pages where people can see and order the products.

Industry/Entity Type

Baby

Requirements
Must have
• beautiful, soft, feminine design. Please use pictures of the colors I'd like: brown, yellow, pink and blue. Any combination, but definitely include brown.

```html
<!DOCTYPE html>
<html lang="en">
<head>
<meta charset="utf-8">
<title>Cozy Cradle Loops</title>
<link href="https://fonts.googleapis.com/css2?family=Open+Sans:wght@400;600;700&family=PT+Serif:wght@400;700&display=swap" rel="stylesheet">
<style>
:root{
  --pink:#ec3d9a;
  --pink-light:#f56bb4;
  --pink-dark:#d92a86;
  --blue:#12b3d6;
  --blue-dark:#0a95b6;
  --gray-text:#555;
  --gray-line:#e6e6e6;
  --footer-bg:#f0f0f1;
  --white:#fff;
}
*{box-sizing:border-box;margin:0;padding:0}
html,body{width:837px;height:1200px;overflow:hidden;background:var(--white)}
body{position:relative;font-family:"PT Serif",Georgia,serif;color:var(--gray-text)}
.abs{position:absolute}

/* header */
.brand{left:100px;top:28px;display:flex;align-items:center;gap:8px}
.brand-dot{width:14px;height:14px;border-radius:50%;background:var(--blue)}
.brand-name{font-size:25px;font-weight:700;color:var(--pink)}
.account{left:597px;top:20px;font-size:10px;color:#666}
.langs{left:683px;top:23px;display:flex;gap:6px}
.langs span{width:12px;height:8px;display:block;border:1px solid #ccc}
.cart{left:524px;top:48px;display:flex;gap:10px;align-items:flex-start}
.cart-label{font-size:8.5px;line-height:13px;color:#666;text-transform:uppercase}
.cart-label b{font-weight:400;color:var(--blue)}
.search{left:637px;top:54px;width:113px;height:19px;border:1px solid #e3e3e3;background:#fafafa;font-size:8px;color:#aaa;padding:4px 8px}
.search svg{position:absolute;right:4px;top:3px}

/* nav */
.nav{left:0;top:93px;width:837px;height:31px;background:linear-gradient(#f77cc0,var(--pink) 45%,var(--pink-dark));display:flex;align-items:center;padding-left:105px;gap:0}
.nav a{font-family:"Open Sans",sans-serif;font-size:8.5px;color:var(--white);text-decoration:none;text-transform:uppercase;margin-right:41px}

/* hero */
.hero{left:88px;top:138px;width:660px;height:268px;border:1px solid var(--gray-line);padding:2px}
.hero-photo{width:100%;height:100%;background:radial-gradient(ellipse at 75% 55%,#5a6a8a 0%,#6d6d6d 35%,#8a8886 70%,#9a9896 100%);position:relative}
.hero h1{position:absolute;left:78px;top:58px;font-family:"Open Sans",sans-serif;font-weight:600;font-size:24px;line-height:34px;color:var(--white)}
.hero p{position:absolute;left:80px;top:138px;width:230px;font-family:"Open Sans",sans-serif;font-size:9px;line-height:17px;color:var(--white)}
.shop-btn{position:absolute;left:82px;top:189px;width:97px;height:28px;background:var(--blue);color:var(--white);font-family:"Open Sans",sans-serif;font-weight:600;font-size:11px;text-align:center;line-height:28px}
.arrow{position:absolute;top:135px;width:28px;height:28px;border-radius:50%;background:var(--white);display:flex;align-items:center;justify-content:center}
.arrow.prev{left:9px}.arrow.next{right:8px}

/* featured */
.featured{left:90px;top:454px;width:657px;height:35px;background:linear-gradient(var(--pink-light),var(--pink));border-radius:2px;color:var(--white);font-weight:700;font-size:15px;padding:8px 14px}
.featured svg{position:absolute;right:10px;top:8px}
.cats{left:90px;top:507px;display:flex;gap:16px}
.cats div{width:146px;font-size:12.5px;color:#444;padding:0 3px 4px;border-bottom:2px solid var(--blue)}
.grid{left:90px;top:545px;display:grid;grid-template-columns:repeat(4,154px);grid-auto-rows:185px;column-gap:13px;row-gap:16px}
.card{border:1px solid #eee;box-shadow:inset 0 0 0 3px #f7f7f7;position:relative}
.card-photo{position:absolute;left:24px;top:12px;width:105px;height:104px}
.card-name{position:absolute;left:12px;top:127px;font-size:11.5px;color:#555}
.card-price{position:absolute;left:12px;top:153px;font-size:13px;color:var(--blue)}
.add-btn{position:absolute;left:71px;top:151px;width:68px;height:20px;background:linear-gradient(#25c2e4,var(--blue-dark));border-radius:2px;color:var(--white);font-size:7.5px;font-weight:700;text-align:center;line-height:20px}

/* promo */
.promo{left:90px;top:957px;width:656px;height:62px;background:linear-gradient(#6f9bd0 0%,#b7d2e6 25%,#e8e4d6 60%,#d9c9a4 100%);box-shadow:0 4px 4px -2px #999}
.promo-tag{position:absolute;right:13px;bottom:9px;font-family:"Open Sans",sans-serif;font-size:7.5px;color:#333}

/* footer */
.footer{left:0;top:1058px;width:837px;height:142px;background:var(--footer-bg)}
.fcol{position:absolute;top:29px}
.fcol h4{font-weight:400;font-size:10px;color:#555;margin-bottom:14px;text-transform:uppercase}
.fcol li{list-style:none;font-size:7.5px;line-height:13px;color:#666;text-transform:uppercase}
.social li{display:flex;align-items:center;gap:11px;line-height:22px}
.social i{width:15px;height:15px;display:block;background:#3b5998}
.email{width:155px;height:22px;border:1px solid #ddd;background:var(--white);font-size:8px;color:#aaa;padding:6px 9px}
.signup{margin:11px 0 0 86px;width:69px;height:20px;background:var(--blue);color:var(--white);font-size:8.5px;text-align:center;line-height:20px}
</style>
</head>
<body>

<header>
  <div class="abs brand"><span class="brand-dot"></span><span class="brand-name">Cozy Cradle Loops</span></div>
  <div class="abs account">Sign in | Register</div>
  <div class="abs langs"><span style="background:#c8d0e6"></span><span style="background:#d9c3c8"></span><span style="background:#d64545;border-top:3px solid #c33"></span><span style="background:#e23"></span></div>
  <div class="abs cart">
    <svg width="30" height="24" viewBox="0 0 30 24"><path d="M1 3h5l3 13h16l3-10H8" fill="none" stroke="#3a7fa8" stroke-width="2"/><circle cx="11" cy="21" r="2" fill="#3a7fa8"/><circle cx="23" cy="21" r="2" fill="#3a7fa8"/></svg>
    <div class="cart-label">Shopping Bag<br><b>(0) Items</b></div>
  </div>
  <div class="abs search">Search...
    <svg width="12" height="12" viewBox="0 0 12 12"><circle cx="5" cy="5" r="3.5" fill="none" stroke="#444" stroke-width="1.5"/><path d="M7.5 7.5l3.5 3.5" stroke="#444" stroke-width="2"/></svg>
  </div>
</header>

<nav class="abs nav">
  <a>Home</a><a>About Us</a><a>Services</a><a>Gallery</a><a>Blog</a><a>Testimonials</a><a>Contact Us</a>
</nav>

<section class="abs hero">
  <div class="hero-photo" role="img" aria-label="Crocheted navy and white baby sneakers on a grey sofa">
    <h1>HANDMADE BABY<br>CROCHETS</h1>
    <p>Neque porro quisquam est qui dolorem ipsum quia dolor sit amet, consectetur, adipisci velit</p>
    <div class="shop-btn">Shop Now</div>
    <div class="arrow prev"><svg width="10" height="12"><path d="M7 1L2 6l5 5" fill="none" stroke="#333" stroke-width="2.4"/></svg></div>
    <div class="arrow next"><svg width="10" height="12"><path d="M3 1l5 5-5 5" fill="none" stroke="#333" stroke-width="2.4"/></svg></div>
  </div>
</section>

<div class="abs featured">Featured Products
  <svg width="19" height="19" viewBox="0 0 19 19"><circle cx="9.5" cy="9.5" r="9.5" fill="#fff"/><path d="M5 9.5h8M9.5 5.5l4 4-4 4" fill="none" stroke="var(--pink)" stroke-width="2.2"/></svg>
</div>

<div class="abs cats"><div>Neque porro</div><div>Quisquam</div><div>Dolorem</div><div>Adipisci velit</div></div>

<main class="abs grid">
  <div class="card"><div class="card-photo" role="img" aria-label="Black crocheted baby sneakers" style="background:linear-gradient(#6b6b6b,#2b2b2b)"></div><div class="card-name">Product Name</div><div class="card-price">$75.00</div><div class="add-btn">ADD TO CART</div></div>
  <div class="card"><div class="card-photo" role="img" aria-label="Pink crocheted baby crown headband" style="background:radial-gradient(#f58bb8,#d7d7d7 70%)"></div><div class="card-name">Product Name</div><div class="card-price">$75.00</div><div class="add-btn">ADD TO CART</div></div>
  <div class="card"><div class="card-photo" role="img" aria-label="Brown crocheted baby sneakers with pink star" style="background:linear-gradient(#8a5d7a,#6d5444 60%,#d8d4cf)"></div><div class="card-name">Product Name</div><div class="card-price">$75.00</div><div class="add-btn">ADD TO CART</div></div>
  <div class="card"><div class="card-photo" role="img" aria-label="Cream crocheted baby shoes with red roses" style="background:radial-gradient(#e6e1d3,#6b6250 90%)"></div><div class="card-name">Product Name</div><div class="card-price">$75.00</div><div class="add-btn">ADD TO CART</div></div>
  <div class="card"><div class="card-photo" role="img" aria-label="Pale pink crocheted baby slippers with flowers" style="background:radial-gradient(#e5a9b8,#c6c3c8 75%)"></div><div class="card-name">Product Name</div><div class="card-price">$75.00</div><div class="add-btn">ADD TO CART</div></div>
  <div class="card"><div class="card-photo" role="img" aria-label="Red crocheted baby shoes with white flowers" style="background:radial-gradient(#d92b2b,#6e2520 90%)"></div><div class="card-name">Product Name</div><div class="card-price">$75.00</div><div class="add-btn">ADD TO CART</div></div>
  <div class="card"><div class="card-photo" role="img" aria-label="Magenta crocheted baby crown headband" style="background:radial-gradient(#e06bd0,#e0e0e0 70%)"></div><div class="card-name">Product Name</div><div class="card-price">$75.00</div><div class="add-btn">ADD TO CART</div></div>
  <div class="card"><div class="card-photo" role="img" aria-label="Mint crocheted baby shoes on tree bark" style="background:radial-gradient(#9fd6cc,#4a4a3c 85%)"></div><div class="card-name">Product Name</div><div class="card-price">$75.00</div><div class="add-btn">ADD TO CART</div></div>
</main>

<aside class="abs promo" role="img" aria-label="Beach banner advertising a holiday trip giveaway">
  <span class="promo-tag"># BANNER ADD</span>
</aside>

<footer class="abs footer">
  <div class="fcol" style="left:93px"><h4>Links</h4><ul><li>BM Press</li><li>BM Catalog</li><li>BM Story</li><li>BM Looks</li></ul></div>
  <div class="fcol" style="left:203px"><h4>Help</h4><ul><li>FAQ</li><li>Your Suggestions</li><li>Contact Us</li></ul></div>
  <div class="fcol" style="left:330px"><h4>Customer Service</h4><ul><li>Terms of Use</li><li>Membership Agreement</li><li>Privacy Policy</li><li>Delivery and Returns</li></ul></div>
  <div class="fcol social" style="left:482px"><h4 style="margin-bottom:8px">Follow Us</h4><ul><li><i></i>Friendbook</li><li><i style="background:#444"></i>Circleplus</li><li><i style="background:#45b3e0"></i>Chirpline</li></ul></div>
  <div class="fcol" style="left:592px"><h4>Newsletter Sign Up!</h4><div class="email">Enter your Email...</div><div class="signup">SIGN UP</div></div>
</footer>

</body>
</html>
```